Small Business Directory Site Requires a Professional Responsive Web Design

Small Business Directory and Coupon Site - we require a complete website design for a brand new responsive & mobile friendly website. We already have a coder who will professional code our website in Magento.

All PSD pages need to be professionally designed then uploaded into a sharedrive (i.e. like filecrate). Additionally, as I cannot pre-empt everything, please note that we may require a little more assistance once the files have been transferred (for example, in www.brightlane-listings.example if you hover your mouse on the search box you will see a pop up box. We want one of these too and I think that means there may be extra design work here)

We have some draft page sketches have been created (there are some minor changes we want to the sketches provided though); however, we require an excellent designer to add the creative touches to it to make it look professionally created. All artwork/font must be legal.

-------------------------
We like the look of the www.brightlane-listings.example and www. marlowfolio.example

For the headers, please consider a font similar to RNS camellia. We likes this style, but it is too thin for the headers...so we need a variation like this one. For the copy/general text font, something basic that marries well with the headers.

---------------------

Please be sure to also read the brief we wrote for the coder as this will help with better understanding our design requirements.

In total I believe we have about 50 pages. This includes all the little pages and most of the pop up boxes (but not the little help key boxes). For example, pages include...

1. Login (this is where customers log in and can edit, manage their profiles. This means that there are backend membership pages)
2. Mini Services (same look and feel as the business coupons)
3. Resource Centre
4. Join (this is where customers learn about the packages available to submit a directory listing, if they ‘buy’ a package (i.e. free, $25 or $150 package) then they can create their own directory listing)
5. Search the directory (customer can view all the categories and also search the directory)
6. Create a directory listing (this is where customers learn about the packages available to submit a directory listing, if they ‘buy’ a package (i.e. free, $25 or $150 package) then they can create their own directory listing)
7. Quote finder (also know as Get a Quote)
8. Coupons (customer go to the business coupon page and can view all current coupons/submit a coupon)
9. Submit a coupon (form)
10.Advertise with us (form)
11. Join the forum
12.Submit an article or video (form)
13. Affiliates (listing of affiliates we currently have)
14. Become an affiliate (form)
15. Case studies (customer can view the case studies we have in the resource centre)
16. Help Guides (customer can view the help guides we have in the resource centre)
17. About Us
18 .Contact Us (form)
19. Terms & Condition
20. Privacy Policy
21. Supporting City Councils
22. Site Map
23. Forgot password / login details
24. Homepage
25. If we hover over a few areas (i.e. search box, location field) it pops up with more information.
etc etc etc. . . there are more pages.

Please see our filecrate link for the draft mock up pages that I have created so far.

https://www.cloudtrunk.example/sh/qk72pmw4rtz8nd/KLMvbTq2fWndxPzs8Yh4ecRQu

We are in a rush! We'd like to get the majority of the artwork completed by the end of the month. Minor fixes/tweaks can occur thereafter.

Target Market(s)

Small Businesses (employees 0 - 50) located throughout Australia

Industry/Entity Type

Business

Font styles to use
Sans Serif

Requirements
Must have
• Professional. Artwork must be legal (cannot be cut and paste or taken off other websites, must be legally purchased and used).Must look contemporary, fresh, modern.

Absolutely must be a responsive site!
Nice to have
• original work, original photos, original art.

like modern, fresh photos that demonstrate innovation, growth, small business, Australian scenery, stability, goals/passion.
Should not have
• cut and paste graphics, illegal graphics, not purchased graphics.

```html
<!DOCTYPE html>
<html lang="en">
<head>
<meta charset="utf-8">
<title>Tradepath Link – Australia's Small Business Support Link</title>
<link href="https://fonts.googleapis.com/css2?family=Open+Sans:wght@400;600;700&family=PT+Serif:wght@400;700&display=swap" rel="stylesheet">
<style>
:root{
  --orange:#f26a0f;
  --orange-light:#f7941d;
  --yellow:#f7b500;
  --green:#3fae2a;
  --ink:#2b2b2b;
  --muted:#8a8a8a;
  --card:#f6f3ee;
  --dark:#1f1c1a;
  --footer:#2a2a2a;
  --footer-bottom:#1c1c1c;
  --white:#ffffff;
}
*{box-sizing:border-box;margin:0;padding:0}
html,body{width:1200px;height:2980px;overflow:hidden}
body{font-family:"Open Sans",Arial,sans-serif;color:var(--ink);background:var(--white);position:relative}

/* hero */
.hero{position:absolute;left:0;top:0;width:1200px;height:740px;
  background:linear-gradient(180deg,#6d4a33 0%,#c98a4e 25%,#8b5e3c 55%,#4a3a33 80%,#3a302c 100%)}
.hero-glow{position:absolute;left:560px;top:0;width:640px;height:520px;
  background:radial-gradient(ellipse at 40% 30%,rgba(255,200,120,.75),rgba(255,160,80,0) 65%)}
.site-header{position:absolute;left:84px;top:0;width:1032px;height:116px;background:rgba(255,255,255,.96)}
.brand{position:absolute;left:30px;top:40px;display:flex;align-items:center;gap:12px}
.brand-mark{width:30px;height:30px;border-radius:50%;background:var(--orange)}
.brand-name{font-size:21px;font-weight:700;color:var(--orange);letter-spacing:.5px}
.main-nav{position:absolute;left:386px;top:64px;display:flex;font-size:11.5px;font-weight:600;color:#333;white-space:nowrap}
.main-nav span{padding:0 9px;border-right:1px solid #999;line-height:14px}
.main-nav span:first-child{padding-left:0}
.main-nav span:last-child{border-right:0;padding-right:0}
.social{position:absolute;left:878px;top:18px;display:flex;gap:4px}
.social i{display:block;width:24px;height:24px;border-radius:3px;background:#4a8fd6}
.social i:nth-child(2){background:#f28c1a}
.social i:nth-child(3){background:#3b5998}
.social i:nth-child(4){background:#1f7bb6}
.social i:nth-child(5){background:#5a7b3a}
.btn-top{position:absolute;top:54px;height:36px;background:var(--orange);color:#fff;font-weight:700;font-size:15px;display:flex;align-items:center;justify-content:center}
.headline{position:absolute;left:110px;top:340px;font-family:"PT Serif",Georgia,serif;color:#fff}
.headline h1{font-size:42px;font-weight:400;line-height:46px}
.headline p{font-size:23px;line-height:28px}
.search-band{position:absolute;left:112px;top:626px;width:978px;height:114px;background:rgba(20,18,18,.88)}
.search-field{position:absolute;top:16px;height:46px;background:#fff;color:#9a9a9a;font-size:13px;display:flex;align-items:center;padding-left:22px}
.search-btn{position:absolute;left:818px;top:16px;width:124px;height:46px;background:var(--green);color:#fff;font-size:16px;font-weight:600;display:flex;align-items:center;justify-content:center}
.search-cats{position:absolute;left:18px;top:78px;font-size:12.5px;color:#ddd;display:flex;gap:14px}
.search-cats .all{color:#fff;font-weight:600;border-left:1px solid #888;padding-left:14px}

/* community */
.section-title{position:absolute;left:0;width:1200px;text-align:center;font-weight:400}
.intro{position:absolute;left:200px;width:800px;top:872px;text-align:center;font-size:13px;line-height:26px;color:#9a9a9a}
.card{position:absolute;top:994px;width:220px;height:248px;background:var(--card);text-align:center;
  border-top:3px dotted #e4ddd2}
.card svg{position:absolute;left:76px;top:34px}
.card h3{position:absolute;left:10px;right:10px;top:134px;font-size:13px;font-weight:600;line-height:18px}
.card p{position:absolute;left:26px;right:26px;top:172px;font-size:12.5px;line-height:16px;color:#7a7a7a}
.rule{position:absolute;top:1330px;height:6px;background:#e7e7e7}
.signup-label{position:absolute;left:420px;top:1323px;font-size:15px;color:#333}
.btn-offer{position:absolute;left:600px;top:1314px;width:174px;height:40px;background:var(--orange);color:#fff;font-size:17px;font-weight:600;display:flex;align-items:center;justify-content:center}

/* why */
.why{position:absolute;left:0;top:1412px;width:1200px;height:602px;background:linear-gradient(90deg,#3a302a,#24201d 50%,#33302e)}
.why-title{position:absolute;left:0;top:60px;width:1200px;text-align:center;color:#fff}
.why-title h2{font-size:44px;font-weight:400}
.why-title p{font-size:19px;color:#ddd;margin-top:6px}
.why-copy{position:absolute;left:114px;top:206px;width:430px;color:#fff}
.why-copy h3{font-size:21px;font-weight:400;color:var(--orange-light);margin-bottom:24px}
.why-copy h3 b{font-weight:600}
.why-copy p{font-size:14px;line-height:19px;margin-bottom:19px}
.btn{display:flex;align-items:center;justify-content:center;font-weight:700;font-size:14px}
.btn-join{position:absolute;left:114px;top:496px;width:114px;height:36px;background:var(--orange);color:#fff}
.phones{position:absolute;left:592px;top:178px;width:422px;height:342px;border-radius:14px;
  background:linear-gradient(135deg,#eeeeee,#8f9aa3 45%,#2c2c2c)}
.dots{position:absolute;left:516px;top:570px;display:flex;gap:6px}
.dots i{width:10px;height:10px;border-radius:50%;background:#fff}
.dots i:first-child{background:var(--orange)}

/* real support */
.sub{position:absolute;left:0;width:1200px;text-align:center;font-size:20px;color:#999}
.col-title{position:absolute;font-size:20px;font-weight:400;text-transform:uppercase}
.tabs{position:absolute;left:148px;top:2290px;width:408px;height:42px;background:#2a2a2a}
.tab-active{position:absolute;left:8px;top:0;width:140px;height:42px;background:var(--orange);color:#fff;font-size:15px;display:flex;align-items:center;justify-content:center}
.tab{position:absolute;left:148px;top:0;width:260px;height:42px;color:#fff;font-size:15px;display:flex;align-items:center;justify-content:center}
.post-img{position:absolute;left:146px;top:2356px;width:192px;height:100px;background:linear-gradient(135deg,#d7c8a6,#6f6a5c 60%,#3e3a30)}
.date-tag{position:absolute;background:var(--orange);color:#fff;font-size:11px;font-weight:700;padding:3px 8px}
.post-text{position:absolute;left:352px;top:2360px;width:200px;font-size:13px;line-height:21px}
.event{position:absolute;left:146px;width:430px;font-size:12.5px;border-bottom:1px solid #ddd;height:46px;display:flex;align-items:center;gap:12px}
.event .date-tag{position:static}
.btn-more{position:absolute;top:2578px;width:114px;height:36px;background:var(--yellow);color:#222}
.why-img{position:absolute;left:620px;top:2282px;width:434px;height:206px;border:2px solid #e6e6e6;
  background:linear-gradient(180deg,#e8eef2,#a9b7c2 45%,#2d3440)}
.affiliate{position:absolute;left:624px;top:2496px;font-size:18px;color:var(--orange);text-transform:uppercase}
.affiliate-text{position:absolute;left:624px;top:2532px;width:440px;font-size:13px;line-height:20px}

/* footer */
.footer{position:absolute;left:0;top:2686px;width:1200px;height:250px;background:var(--footer);color:#ddd}
.fcol{position:absolute;top:34px;font-size:12.5px;line-height:27px}
.fcol h4{font-size:15px;font-weight:600;color:#fff;margin-bottom:10px;line-height:20px}
.subscribe-box{position:absolute;left:870px;top:132px;width:220px;height:36px;background:#fff;font-size:11px;color:#aaa;display:flex;align-items:center;padding-left:10px}
.subscribe-btn{position:absolute;right:4px;top:5px;width:64px;height:26px;background:var(--yellow);color:#222;font-size:12px;font-weight:700;display:flex;align-items:center;justify-content:center}
.footer-bottom{position:absolute;left:0;top:2936px;width:1200px;height:44px;background:var(--footer-bottom);color:#bbb;font-size:12.5px;text-align:center;line-height:44px}
</style>
</head>
<body>

<section class="hero" role="img" aria-label="Photo of a woman looking over a lake at sunset">
  <div class="hero-glow"></div>
</section>

<header class="site-header">
  <div class="brand"><span class="brand-mark"></span><span class="brand-name">TRADEPATH LINK</span></div>
  <div class="social"><i></i><i></i><i></i><i></i><i></i></div>
  <nav class="main-nav"><span>Coupons</span><span>Mini Services</span><span>Get A Quote</span><span>Advertise</span><span>Resource Centre</span></nav>
  <div class="btn-top" style="left:838px;width:78px">JOIN</div>
  <div class="btn-top" style="left:924px;width:82px">LOGIN</div>
</header>

<div class="headline">
  <h1>Let Us Help You Grow</h1>
  <p>Australia’s Small Business Support Link</p>
</div>

<div class="search-band">
  <div class="search-field" style="left:16px;width:376px">What are you looking for</div>
  <div class="search-field" style="left:393px;width:410px">
    <svg width="10" height="14" viewBox="0 0 10 14" style="margin-right:10px"><path d="M5 0a5 5 0 0 0-5 5c0 4 5 9 5 9s5-5 5-9a5 5 0 0 0-5-5z" fill="#bbb"/><circle cx="5" cy="5" r="2" fill="#fff"/></svg>Where</div>
  <div class="search-btn">SEARCH NOW</div>
  <div class="search-cats"><span>Banking</span><span>Finance &amp; Insurance</span><span>Marketing</span><span>Design</span><span>Photography</span><span>Video</span><span class="all">VIEW ALL</span></div>
</div>

<h2 class="section-title" style="top:830px;font-size:29px">Get Real Support from Our Community</h2>
<p class="intro">Lorem ipsum dolor sit amet, consectetur adipiscing elit, sed do eiusmod tempor incididunt ut labore et dolore magna aliqua. Ut enim ad minim veniam, quis nostrud exercitation ullamco laboris nisi ut aliquip ex ea commodo consequat.</p>

<div class="card" style="left:112px">
  <svg width="68" height="68" viewBox="0 0 68 68"><circle cx="34" cy="14" r="7" fill="#333"/><circle cx="14" cy="24" r="6" fill="#333"/><circle cx="54" cy="24" r="6" fill="#333"/><circle cx="30" cy="36" r="14" fill="none" stroke="#333" stroke-width="4"/><circle cx="30" cy="36" r="8" fill="var(--orange)"/><path d="M40 46l14 14" stroke="#333" stroke-width="6" stroke-linecap="round"/></svg>
  <h3>How Did You Sort<br>Your Business</h3>
  <p>Text your name and number to 123123 to receive updates</p>
</div>
<div class="card" style="left:362px">
  <svg width="68" height="68" viewBox="0 0 68 68"><circle cx="32" cy="36" r="22" fill="none" stroke="#333" stroke-width="4"/><path d="M22 36l8 8 14-16" fill="none" stroke="var(--orange)" stroke-width="5"/><rect x="28" y="8" width="8" height="6" fill="#333"/><text x="44" y="62" font-family="Open Sans,sans-serif" font-size="14" font-weight="700" fill="var(--orange)">24</text></svg>
  <h3>Why Go with Tradepath Link?</h3>
  <p>Text your name and number to 123123 to receive updates</p>
</div>
<div class="card" style="left:616px">
  <svg width="68" height="68" viewBox="0 0 68 68"><circle cx="34" cy="34" r="12" fill="var(--orange)"/><g stroke="#333" stroke-width="3"><path d="M34 22V8M34 46v14M22 34H8M46 34h14M25 25l-9-9M43 25l9-9M25 43l-9 9M43 43l9 9"/></g><g fill="#333"><circle cx="34" cy="7" r="4"/><circle cx="34" cy="61" r="4"/><circle cx="7" cy="34" r="4"/><circle cx="61" cy="34" r="4"/></g></svg>
  <h3>Become an Affiliate</h3>
  <p>Text your name and number to 123123 to receive updates</p>
</div>
<div class="card" style="left:868px">
  <svg width="68" height="68" viewBox="0 0 68 68"><rect x="20" y="12" width="26" height="46" rx="4" fill="none" stroke="#333" stroke-width="4"/><circle cx="33" cy="52" r="2" fill="#333"/><circle cx="46" cy="14" r="9" fill="var(--orange)"/><path d="M42 14l3 3 5-6" stroke="#fff" stroke-width="2" fill="none"/></svg>
  <h3>Join Mobile Vantage Club</h3>
  <p>Text your name and number to 123123 to receive updates</p>
</div>

<div class="rule" style="left:112px;width:264px"></div>
<div class="rule" style="left:820px;width:268px"></div>
<div class="signup-label">Signup for Daily Deals</div>
<div class="btn-offer">Submit An Offer</div>

<section class="why" role="img" aria-label="Dim photo of a café interior">
  <div class="why-title"><h2>Why Tradepath Link?</h2><p>Australia’s Small Business Support Link</p></div>
  <div class="why-copy">
    <h3>Promote and <b>Support you</b></h3>
    <p>Our purpose is to link, promote and support you.<br>We’re focused on only business to business service.<br>Our directory gives members more purchasing choice and selling reach.We actively promote members with our daily deals, resource centre, newsletter and advertising.<br>We provide real support via our online forums, networks and newsletter.</p>
    <p>To sum it up, we link members together to secure sales.</p>
    <p>Become part of our supportive community. A community made up of real business owners just like you!</p>
  </div>
  <div class="btn btn-join">JOIN NOW</div>
  <div class="phones" role="img" aria-label="Three smartphones showing member directory listings"></div>
  <div class="dots"><i></i><i></i><i></i><i></i><i></i></div>
</section>

<h2 class="section-title" style="top:2074px;font-size:44px">Get Real Support</h2>
<p class="sub" style="top:2138px">Neque porro quisquam est qui dolorem ipsum</p>

<h3 class="col-title" style="left:148px;top:2250px">Business Spotlight</h3>
<div class="tabs"><div class="tab-active">Daily Events</div><div class="tab">Events Calender</div></div>
<div class="post-img" role="img" aria-label="Photo of a business seminar room"></div>
<div class="date-tag" style="left:274px;top:2436px">21 JUNE</div>
<p class="post-text">What is leadership? How does poor leadership affect business start of blog post or resource post to get them interesting in reading....</p>
<div class="event" style="top:2470px;border-top:1px solid #ddd"><span class="date-tag">22 JUNE</span>Lorem Ipsum dolor sit amet and typesetting industry</div>
<div class="event" style="top:2516px"><span class="date-tag">26 JUNE</span>Lorem Ipsum dolor sit amet and typesetting industry</div>
<div class="btn btn-more" style="left:146px">Read More</div>

<h3 class="col-title" style="left:620px;top:2250px">Why TPL?</h3>
<div class="why-img" role="img" aria-label="Photo of business people shaking hands"></div>
<div class="affiliate">Affiliate ABC Brand</div>
<p class="affiliate-text">We are collaborating with networking groups around the country to bring our members more support and greater choice</p>
<div class="btn btn-more" style="left:624px">Read More</div>

<footer class="footer">
  <div class="fcol" style="left:108px"><h4>SITE DIRECTORY</h4>Search the Directory<br>Create a Directory Listing<br>Quote Finder<br>Coupons<br>Submite A Coupons<br>Advertise with US</div>
  <div class="fcol" style="left:314px"><h4>RESOURCES</h4>Joine the forum<br>submit an Article or video<br>Affiliates<br>Become an Affiliate<br>Case Studies<br>Help Guides</div>
  <div class="fcol" style="left:504px;width:160px"><h4>CATEGORIES</h4>Lorem ipsum dolor sit consectetur adipiscing elit, sed do eiusmod tempor incididunt labore</div>
  <div class="fcol" style="left:688px"><h4>ABOUT</h4>About Us<br>Contact Us<br>Terms and Conditions<br>Privacy Policy<br>Supporting City Councils<br>Site map</div>
  <div class="fcol" style="left:870px;width:230px"><h4>SUBSCRIBE US</h4>Receive our latest offers, stories &amp; event news, direct to your inbox</div>
  <div class="subscribe-box">Enter email address<div class="subscribe-btn">SIGN UP</div></div>
</footer>
<div class="footer-bottom">Copyrights © 2014 tradepathlink.example - All Rights Reserved</div>

</body>
</html>
```